Roofing company in Toronto, Canada needs a logo design and business card design

We need a business card and logo created for our company. Our company is "KLV Roofing" which provides roofing services for commercial and residential customers. We serve customers in the Greater Toronto Area (in Canada) thus the name KLV.

We want the logo and business card to be a modern design displaying professionalism and quality in the work. We would prefer rounded corners for the business cards but are open to other ideas. The cards should be pleasant and appealing to customers.

Target Market(s)

Commercial and Residential customers

Industry/Entity Type

Roofing

Contact Information for Business Card

Logo Text

KLV Roofing

Requirements
Nice to have
• Colours that are pleasing to the eye but at the same time should stand out from other business cards. If the design can incorporate the name of KLV Roofing and the actual concept of roofing that would be nice.
Should not have
• Do not want the business cards or logo to be childish looking. Need to look professionally designed.

```html
<!DOCTYPE html>
<html lang="en">
<head>
<meta charset="utf-8">
<title>KLV Roofing – Business Card</title>
<link href="https://fonts.googleapis.com/css2?family=Open+Sans:wght@400;600&display=swap" rel="stylesheet">
<style>
  :root {
    --backdrop: #4a423d;
    --card: #0f0f0f;
    --gold: #e8a912;
    --white: #f2f2f2;
    --silver: #c9c9c9;
  }
  html, body {
    margin: 0;
    padding: 0;
    width: 1200px;
    height: 900px;
    overflow: hidden;
    background: var(--backdrop);
    font-family: "Open Sans", Arial, sans-serif;
  }
  .canvas {
    position: relative;
    width: 1200px;
    height: 900px;
  }
  .card {
    position: absolute;
    top: 307px;
    width: 500px;
    height: 286px;
    background: var(--card);
    border-radius: 10px;
    box-shadow: 0 10px 30px rgba(0,0,0,0.45);
    overflow: hidden;
  }
  .card-back { left: 70px; }
  .card-front { left: 630px; }

  /* Contact side: brand block fills the left half with strong weight */
  .brand-block {
    position: absolute;
    left: 44px;
    top: 0;
    height: 100%;
    width: 200px;
    display: flex;
    align-items: center;
    gap: 14px;
  }
  .brand-square {
    width: 30px;
    height: 30px;
    background: var(--gold);
    flex: none;
    align-self: center;
  }
  .brand-name {
    color: var(--gold);
    font-weight: 600;
    font-size: 40px;
    line-height: 1.05;
    letter-spacing: 0.5px;
  }
  .brand-name span { display: block; }

  .contact {
    position: absolute;
    left: 262px;
    top: 56px;
    color: var(--white);
    font-size: 12.5px;
    line-height: 1.35;
  }
  .contact-name {
    color: var(--gold);
    font-size: 19px;
    line-height: 1.1;
    margin: 0;
    font-weight: 400;
  }
  .contact-title { margin: 2px 0 18px; }
  .contact-address { margin: 0 0 16px; }
  .contact-list {
    list-style: none;
    margin: 0;
    padding: 0;
  }
  .contact-list li {
    display: flex;
    align-items: center;
    gap: 8px;
  }
  .contact-icon {
    width: 10px;
    height: 10px;
    flex: none;
  }

  /* Logo side */
  .card-front {
    display: flex;
    align-items: center;
    justify-content: center;
  }
  .front-name {
    color: var(--silver);
    font-weight: 600;
    font-size: 54px;
    line-height: 1.05;
    letter-spacing: 1px;
    text-align: left;
  }
  .front-name span { display: block; }
</style>
</head>
<body>
<main class="canvas">
  <section class="card card-back" aria-label="Contact side">
    <div class="brand-block">
      <span class="brand-square"></span>
      <span class="brand-name"><span>KLV</span><span>Roofing</span></span>
    </div>
    <div class="contact">
      <h1 class="contact-name">Daniel Morris</h1>
      <p class="contact-title">Managing Director</p>
      <p class="contact-address">48 Lakeshore Road West<br>Toronto, ON M5V 2T6.</p>
      <ul class="contact-list">
        <li>
          <svg class="contact-icon" viewBox="0 0 10 10"><path fill="#e8a912" d="M2 0.5l1.6 2.2-0.9 1.1c0.6 1.2 1.4 2 2.5 2.6l1.1-0.9 2.2 1.6-0.8 1.9C4.6 9 1 5.4 0.1 1.3z"/></svg>
          044-555 018 272
        </li>
        <li>
          <svg class="contact-icon" viewBox="0 0 10 10"><rect x="0" y="2" width="10" height="6.5" fill="#e8a912"/><path d="M0 2l5 3.6L10 2" fill="none" stroke="#0f0f0f" stroke-width="0.9"/></svg>
          info@klvroofing.com
        </li>
        <li>
          <svg class="contact-icon" viewBox="0 0 10 10"><g fill="none" stroke="#e8a912" stroke-width="1.4"><rect x="0.8" y="4.2" width="5" height="2.6" rx="1.3" transform="rotate(-45 3.3 5.5)"/><rect x="4.2" y="3.2" width="5" height="2.6" rx="1.3" transform="rotate(-45 6.7 4.5)"/></g></svg>
          www.klvroofing.com
        </li>
      </ul>
    </div>
  </section>

  <section class="card card-front" aria-label="Logo side">
    <span class="front-name"><span>KLV</span><span>Roofing</span></span>
  </section>
</main>
</body>
</html>
```